TuneRoost - Music Industry App needs a top quality wordpress homepage

We need a modern responsive wordpress homepage built. Our website will only feature one page with the goal to get people to sign up to our app. A word document has been uploaded outlining the page content/sections.

Once the homepage is finalised, I will also need 2 landing pages built as part of this competition. It will be very similar to the homepage with the same layout etc but just feature different images and content. The homepage is for anyone (artists and venues) to find out about us but the landing pages will be artist or venue specific.

The completed work must be delivered as an exportable file into wordpress and be designed properly so no more work is needed to begin utilising as the actual website. The images used must be setup correctly for speed and quality also.

Target Market(s)

Venues and Artists.

Coding

Coded - Design and coding required

Requirements
Must have
• UPDATE: High Res Logo files attached
• Must be a modern looking website and be responsive. Must look good across all devices from desktop, to mobile and tablet. Needs to be very high quality.
• Please see the attached logo - I am waiting for the final high quality version and will reupload when complete but this will be enough to get you started for now. The website must have a dark base colour and have red/white elements to match the logo. The red colour used MUST match the red colour used in the logo.
• Please have a go at creating it how you think is best and provide feedback from there. I am leaving it very open to the designers so I can get the best website possible and lots of different ideas etc.

```html
<!DOCTYPE html>
<html lang="en">
<head>
<meta charset="utf-8">
<title>TuneRoost – Live Music Booking</title>
<link rel="stylesheet" href="https://fonts.googleapis.com/css2?family=Jost:wght@400;500;600;700&family=League+Spartan:wght@600;700&display=swap">
<style>
  :root{
    --red:#e1061b;
    --red-deep:#b8000e;
    --red-soft:#d9303c;
    --black:#050505;
    --ink:#0d0d10;
    --white:#ffffff;
    --grey:#8b8b8b;
    --line:#3a3a3a;
  }
  *{box-sizing:border-box;margin:0;padding:0}
  html,body{width:1200px;height:4444px;overflow:hidden;background:var(--black)}
  body{position:relative;font-family:"Jost",sans-serif;color:var(--white)}
  .abs{position:absolute}
  h1,h2,h3{font-family:"League Spartan",sans-serif;font-weight:700;line-height:1}
  .red{color:var(--red)}

  /* nav */
  .nav{left:0;top:0;width:1200px;height:115px;background:#000;border-bottom:2px solid var(--red);z-index:5}
  .nav a{position:absolute;top:48px;font-size:15px;font-weight:600;color:var(--white);text-decoration:none}
  .brand-badge{left:488px;top:-10px;width:224px;height:224px;border-radius:50%;background:#000;border:3px solid var(--red);z-index:6;display:flex;align-items:center;justify-content:center}
  .brand-badge span{font-size:38px;font-weight:500;color:var(--red);margin-top:20px}

  /* hero */
  .hero{left:0;top:0;width:1200px;height:1043px;clip-path:polygon(0 0,100% 0,100% 1043px,50% 857px,0 1043px);
    background:radial-gradient(ellipse at 50% 30%,#4a4650 0%,#24222a 40%,#0e0d12 80%),#111;z-index:2}
  .hero-title{left:0;top:448px;width:1200px;text-align:center;font-size:58px;color:var(--red);z-index:4}
  .hero-sub{left:0;top:530px;width:1200px;text-align:center;font-size:23px;font-weight:500;z-index:4}
  .btn-solid{display:flex;align-items:center;justify-content:center;background:var(--red);color:var(--white);border-radius:30px;font-weight:600}
  .hero-btn{left:475px;top:583px;width:250px;height:58px;font-size:19px;z-index:4}
  .hero-edge{left:0;top:0;z-index:3}
  .divider-dot{left:552px;top:809px;width:96px;height:96px;border-radius:50%;background:#000;border:3px solid var(--red);z-index:4}

  /* how */
  .how{left:0;top:857px;width:1200px;height:808px;background:#060606;z-index:1}
  .how-photo{right:0;top:220px;width:600px;height:588px;background:radial-gradient(ellipse at 70% 45%,#5a5a5a 0%,#262626 35%,#060606 75%)}
  .how-title{left:112px;top:1048px;font-size:70px;z-index:3}
  .how-title span{display:block;margin-top:4px}
  .how-intro{left:112px;top:1200px;width:480px;font-size:13px;line-height:29px;color:var(--grey);z-index:3}
  .steps{left:112px;top:1322px;list-style:none;z-index:3}
  .steps li{height:61px;display:flex;align-items:flex-start;font-size:14px}
  .steps li i{width:24px;height:24px;border-radius:50%;border:3px solid var(--red);background:#000;margin-right:28px;margin-top:-4px}

  /* why */
  .why{left:0;top:1665px;width:1200px;height:680px;background:linear-gradient(#07070a,#0c0c12 60%,#08080b)}
  .why-title{left:0;top:1740px;width:1200px;text-align:center;font-size:58px}
  .feature{top:1908px;width:230px;text-align:center}
  .feature .ring{width:132px;height:132px;margin:0 auto;border-radius:50%;background:var(--red);padding:10px 10px 10px 14px}
  .feature .ring div{width:100%;height:100%;border-radius:50%;background:radial-gradient(circle at 40% 35%,#fff,#cfcfcf);display:flex;align-items:center;justify-content:center}
  .feature h3{font-family:"Jost",sans-serif;font-weight:600;font-size:23px;color:var(--red);margin-top:16px}
  .feature p{font-size:12px;line-height:23px;margin-top:10px}

  /* red band */
  .band{left:0;top:2225px;width:1200px;height:1242px;clip-path:polygon(0 112px,100% 0,100% 1147px,0 1242px);
    background:linear-gradient(160deg,#c4000f 0%,#b5000c 45%,#d80a1c 70%,#b0000c 100%)}
  .photo-ring{width:344px;height:344px;border-radius:50%;border:9px solid var(--red-soft)}
  .photo-ring div{width:100%;height:100%;border-radius:50%}
  .venue-photo{left:149px;top:2402px}
  .venue-photo div{background:radial-gradient(circle at 50% 25%,#f4efc8 0%,#8d7c4a 30%,#2a2418 65%,#0b0a08 100%)}
  .artist-photo{left:708px;top:2947px}
  .artist-photo div{background:radial-gradient(circle at 55% 45%,#8a7158 0%,#2d3a6a 40%,#121a38 75%,#05060d 100%)}
  .ticks{list-style:none;font-size:13px}
  .ticks li{height:41px;display:flex;align-items:flex-start}
  .ticks svg{margin-right:18px;margin-top:2px;flex:none}
  .band-note{font-size:13px;line-height:29px}
  .btn-line{display:flex;align-items:center;justify-content:center;border:2px solid var(--white);border-radius:26px;font-size:15px;font-weight:500}

  /* about */
  .about{left:0;top:3372px;width:1200px;height:700px;background:linear-gradient(#0c0b0d,#080808)}
  .about-title{left:0;top:3525px;width:1200px;text-align:center;font-size:58px}
  .about-text{left:260px;top:3620px;width:680px;text-align:center;font-size:13px;line-height:30px}
  .about-btn{left:502px;top:3769px;width:196px;height:57px;font-size:19px}
  .foot-brand{left:880px;top:3930px;display:flex;align-items:center;gap:14px}
  .foot-brand i{width:52px;height:52px;border-radius:50%;border:5px solid var(--red)}
  .foot-brand span{font-size:44px;font-weight:500;color:var(--red)}

  /* footer */
  .footer{left:0;top:4072px;width:1200px;height:372px;background:#080808}
  .foot-h{top:4102px;font-family:"Jost",sans-serif;font-size:22px;font-weight:500;letter-spacing:.5px}
  .field{background:var(--white);color:#222;font-size:11px;padding:9px 12px;height:35px}
  .submit{left:112px;top:4309px;width:98px;height:33px;background:var(--red);font-size:12px;display:flex;align-items:center;justify-content:center}
  .contact-item{left:552px;display:flex;align-items:flex-start}
  .contact-item .ico{width:42px;height:42px;border-radius:50%;border:2px solid var(--white);display:flex;align-items:center;justify-content:center;margin-right:18px;flex:none}
  .contact-item b{display:block;font-weight:500;font-size:13px;letter-spacing:.5px}
  .contact-item small{font-size:12px;color:#c9c9c9}
  .follow-text{left:869px;top:4162px;width:230px;font-size:11px;line-height:26px}
  .social{top:4252px;width:36px;height:36px;border-radius:50%;border:2px solid var(--white)}
  .rule{left:112px;top:4373px;width:976px;height:1px;background:var(--line)}
  .copy{left:0;top:4398px;width:1200px;text-align:center;font-size:14px}
</style>
</head>
<body>

<!-- hero -->
<section class="abs hero" role="img" aria-label="Photo of a singer performing live with a drummer and guitarist on a dim stage"></section>
<svg class="abs hero-edge" width="1200" height="1060" viewBox="0 0 1200 1060"><polyline points="0,1043 600,857 1200,1043" fill="none" stroke="#e1061b" stroke-width="2"/></svg>

<header class="abs nav">
  <a style="left:176px" href="#">Home</a>
  <a style="left:262px" href="#">About Us</a>
  <a style="left:375px" href="#">Services</a>
  <a style="left:744px" href="#">News</a>
  <a style="left:828px" href="#">Testimonial</a>
  <a style="left:959px" href="#">Contact Us</a>
</header>
<div class="abs brand-badge"><span>TuneRoost</span></div>

<h1 class="abs hero-title">Zoomly for Live Music</h1>
<p class="abs hero-sub">TuneRoost connects venues with artists to make booking gigs simple</p>
<a class="abs btn-solid hero-btn">Sign up now for FREE</a>
<div class="abs divider-dot"></div>

<!-- how it works -->
<section class="abs how">
  <div class="abs how-photo" role="img" aria-label="Close-up photo of a hand on guitar strings"></div>
</section>
<h2 class="abs how-title">How<span><span class="red" style="display:inline">TuneRoost</span> Works</span></h2>
<p class="abs how-intro">Sed ut perspiciatis unde omnis iste natus error sit voluptatem accusantium dolo remque laudantium, totam rem aperiam, eaque ipsa quae ab illo invenv quasi architecto beatae vitae dicta sunt explicabo.</p>
<ul class="abs steps">
  <li><i></i>Artists and venues sign up for free and create a profile</li>
  <li><i></i>Venues search for an artist for their upcoming gigs</li>
  <li><i></i>Venues request a quote and communicate with the artist direct</li>
  <li><i></i>The gig is booked in once payment is provided by the venue.</li>
  <li><i></i>Upon completion the money is paid to the artist within 48 hours or less.</li>
</ul>

<!-- why -->
<section class="abs why" role="img" aria-label="Dark faded photo of DJ equipment"></section>
<h2 class="abs why-title">Why <span class="red">TuneRoost?</span></h2>

<div class="abs feature" style="left:120px">
  <div class="ring"><div><svg width="56" height="56" viewBox="0 0 56 56" fill="none" stroke="#333" stroke-width="3"><path d="M22 40V12l22-5v28"/><circle cx="16" cy="40" r="6"/><circle cx="38" cy="35" r="6"/></svg></div></div>
  <h3>Simple</h3>
  <p>TuneRoost makes gig booking easy<br>for both the venue &amp; artist</p>
</div>
<div class="abs feature" style="left:363px">
  <div class="ring"><div><svg width="56" height="56" viewBox="0 0 56 56" fill="none" stroke="#333" stroke-width="3"><rect x="6" y="26" width="24" height="12" rx="6" transform="rotate(-45 18 32)"/><rect x="26" y="18" width="24" height="12" rx="6" transform="rotate(-45 38 24)"/><path d="M22 34l12-12"/></svg></div></div>
  <h3>Connect</h3>
  <p>Join the TuneRoost community which<br>is full of amazing artists and<br>venues</p>
</div>
<div class="abs feature" style="left:608px">
  <div class="ring"><div><svg width="56" height="56" viewBox="0 0 56 56"><path d="M28 6l18 7v13c0 12-8 20-18 24-10-4-18-12-18-24V13z" fill="none" stroke="#333" stroke-width="3"/><path d="M28 12l12 5v9c0 9-5 15-12 18z" fill="#333"/></svg></div></div>
  <h3>Protection</h3>
  <p>Everyone is protected with our<br>complimentary dispute resolutions</p>
</div>
<div class="abs feature" style="left:853px">
  <div class="ring"><div><svg width="56" height="56" viewBox="0 0 56 56" fill="none" stroke="#333" stroke-width="3"><path d="M30 8h16v16L24 46 8 30z"/><circle cx="39" cy="15" r="3"/><path d="M18 30l8 8M22 26l8 8"/></svg></div></div>
  <h3>Price</h3>
  <p>Get the best rate possible with<br>TuneRoost only receiving 5% of the<br>artists fee</p>
</div>

<!-- venues & artists -->
<section class="abs band" role="img" aria-label="Red-toned faded photo of DJ decks"></section>

<div class="abs photo-ring venue-photo"><div role="img" aria-label="Photo of a concert crowd under bright stage lights"></div></div>
<h2 class="abs" style="left:540px;top:2392px;font-size:48px">Venues</h2>
<ul class="abs ticks" style="left:552px;top:2476px">
  <li><svg width="14" height="12" viewBox="0 0 14 12"><path d="M1 6l4 4 8-9" fill="none" stroke="#fff" stroke-width="2.5"/></svg>TuneRoost is a 100% FREE service for all venues - you pay us nothing!</li>
  <li><svg width="14" height="12" viewBox="0 0 14 12"><path d="M1 6l4 4 8-9" fill="none" stroke="#fff" stroke-width="2.5"/></svg>Get instant access to hundreds of artists around your local community</li>
  <li><svg width="14" height="12" viewBox="0 0 14 12"><path d="M1 6l4 4 8-9" fill="none" stroke="#fff" stroke-width="2.5"/></svg>All genres to suit any venue from a pub to a wedding or even a nightclub</li>
  <li><svg width="14" height="12" viewBox="0 0 14 12"><path d="M1 6l4 4 8-9" fill="none" stroke="#fff" stroke-width="2.5"/></svg>Simple booking process with a money back guarantee</li>
  <li><svg width="14" height="12" viewBox="0 0 14 12"><path d="M1 6l4 4 8-9" fill="none" stroke="#fff" stroke-width="2.5"/></svg>Communicate directly with the artist and negotiate the price</li>
</ul>
<p class="abs band-note" style="left:552px;top:2681px;width:540px">TuneRoost is not yet ready to host gigs as we're currently working on building our artists. We are launching for venues in Q4 2019. Pre-register now to keep informed &amp; be one of the first people to use our platform.</p>
<a class="abs btn-line" style="left:552px;top:2808px;width:210px;height:48px">Email Registeration</a>

<h2 class="abs" style="left:129px;top:2933px;font-size:48px">Artists</h2>
<ul class="abs ticks" style="left:131px;top:3016px">
  <li><svg width="14" height="12" viewBox="0 0 14 12"><path d="M1 6l4 4 8-9" fill="none" stroke="#fff" stroke-width="2.5"/></svg>Sign up to TuneRoost for FREE and get yourself in front of venues</li>
  <li><svg width="14" height="12" viewBox="0 0 14 12"><path d="M1 6l4 4 8-9" fill="none" stroke="#fff" stroke-width="2.5"/></svg>Only pay us if you get a gig - we only get 5% of the fee you charge the venue</li>
  <li><svg width="14" height="12" viewBox="0 0 14 12"><path d="M1 6l4 4 8-9" fill="none" stroke="#fff" stroke-width="2.5"/></svg>All genres and artists welcome - as long as you're experienced and professional</li>
  <li><svg width="14" height="12" viewBox="0 0 14 12"><path d="M1 6l4 4 8-9" fill="none" stroke="#fff" stroke-width="2.5"/></svg>Get paid within 48 hours or less after the gig guaranteed!</li>
  <li><svg width="14" height="12" viewBox="0 0 14 12"><path d="M1 6l4 4 8-9" fill="none" stroke="#fff" stroke-width="2.5"/></svg>Negotiate your price and don't pay huge agent fees to ensure you earn top dollar</li>
</ul>
<p class="abs band-note" style="left:131px;top:3221px">Sign up and create your TuneRoost profile now</p>
<a class="abs btn-line" style="left:131px;top:3281px;width:210px;height:48px">Email Registeration</a>
<div class="abs photo-ring artist-photo"><div role="img" aria-label="Photo of a guitarist performing on a blue-lit stage"></div></div>

<!-- about -->
<section class="abs about" style="z-index:-1"></section>
<h2 class="abs about-title">About <span class="red">TuneRoost</span></h2>
<p class="abs about-text">Sed ut perspiciatis unde omnis iste natus error sit voluptatem accusantium doloremque laudantium, totam rem aperiam, eaque ipsa quae ab illo inventore veritatis et quasi architecto beatae vitae dicta sunt explicabo. Nemo enim ipsam voluptatem quia voluptas sit aspernatur aut odit aut fugit, sed quia consequuntur magni dolores eos qui ratione voluptatem sequi nesciunt.</p>
<a class="abs btn-solid about-btn">Read More</a>
<div class="abs foot-brand"><i></i><span>TuneRoost</span></div>

<!-- footer -->
<footer class="abs footer"></footer>
<h3 class="abs foot-h" style="left:112px">CONTACT US</h3>
<div class="abs field" style="left:112px;top:4156px;width:180px">First Name :</div>
<div class="abs field" style="left:302px;top:4156px;width:180px">Last Name :</div>
<div class="abs field" style="left:112px;top:4200px;width:180px">Email :</div>
<div class="abs field" style="left:302px;top:4200px;width:180px">Phone :</div>
<div class="abs field" style="left:112px;top:4244px;width:370px;height:54px">Message :</div>
<div class="abs submit">SUBMIT</div>

<h3 class="abs foot-h" style="left:560px">ADDRESS</h3>
<div class="abs contact-item" style="top:4150px">
  <div class="ico"><svg width="14" height="18" viewBox="0 0 14 18"><path d="M7 1a6 6 0 0 0-6 6c0 4.5 6 10 6 10s6-5.5 6-10a6 6 0 0 0-6-6z" fill="none" stroke="#fff" stroke-width="1.8"/><circle cx="7" cy="7" r="2" fill="#fff"/></svg></div>
  <div><b>ADDRESS</b><small># Lorem Ipsum Dummy Lorem</small></div>
</div>
<div class="abs contact-item" style="top:4213px">
  <div class="ico"><svg width="16" height="16" viewBox="0 0 16 16"><path d="M3 1l3 3-2 2c1 2 3 4 6 6l2-2 3 3-2 2C7 15 1 9 1 3z" fill="#fff"/></svg></div>
  <div><b>PHONE NUMBER</b><small>000-555-0142</small></div>
</div>
<div class="abs contact-item" style="top:4272px">
  <div class="ico"><svg width="18" height="14" viewBox="0 0 18 14"><rect x="1" y="1" width="16" height="12" fill="#fff"/><path d="M1 1l8 6 8-6" fill="none" stroke="#080808" stroke-width="1.5"/></svg></div>
  <div><b>EMAIL US</b><small>info@tuneroost.com/</small></div>
</div>

<h3 class="abs foot-h" style="left:869px">FOLLOW US</h3>
<p class="abs follow-text">Sed ut perspiciatis unde omnis iste natus error sit voluptatem accusantium dolor to tam rem aperiam</p>
<div class="abs social" style="left:867px"></div>
<div class="abs social" style="left:910px"></div>
<div class="abs social" style="left:953px"></div>
<div class="abs social" style="left:996px"></div>
<div class="abs social" style="left:1039px"></div>

<div class="abs rule"></div>
<p class="abs copy">Copyrights © 2019 TuneRoost.All Rights Reserved</p>

</body>
</html>
```